Laser Tattoo Removal Business Cards

We are looking for a professional business card design for a laser tattoo removal business. Ideally looking for a black business card design. The name of the business is Brightline Tattoo Removal. We place our cards at local tattoo shops so we ideally are looking for something trendy/edgy to draw both male and female clientele in.

Target Market(s)

Male/Female ages 18-60

Contact Information for Business Card

black background ideally.. hoping to stay within greys, whites and black

Font styles to use
Serif
Sans Serif

Colors
121212
a9a9a9
5c5c5c
f5f5f5
ffffff
7f7f7f
606060
848484
9d9d9d

Requirements
Must have
• Employee Info:
• Melissa Thornbury
• Chief Executive Offer
• m: 919.537.2846
• w: 919.362.4178
• f: 919.685.3907
• mthornbury@brightlinetattooremoval.example
• Address:
• 4615 Oakmere Pkwy, Suite 210
• Raleigh, NC 27654
• Website:
• www.brightlinetattooremoval.example
Nice to have
• Myabe business name on back or logo on back and employee info on the front

```html
<!DOCTYPE html>
<html lang="en">
<head>
<meta charset="utf-8">
<title>Brightline Tattoo Removal — Business Cards</title>
<link rel="stylesheet" href="https://fonts.googleapis.com/css2?family=Josefin+Sans:wght@400;600&family=Lato:wght@300;400;700&display=swap">
<style>
  :root {
    --ink: #121212;
    --stage: #2a2a2a;
    --paper: #f5f5f5;
    --white: #ffffff;
    --grey-mid: #7f7f7f;
    --grey-light: #a9a9a9;
    --grey-dark: #5c5c5c;
  }
  * { box-sizing: border-box; margin: 0; padding: 0; }
  html, body { width: 1200px; height: 900px; overflow: hidden; }
  body {
    background: var(--stage);
    display: flex;
    flex-direction: column;
    align-items: center;
    justify-content: center;
    gap: 50px;
    font-family: "Lato", sans-serif;
  }
  .card {
    width: 630px;
    height: 360px;
    border-radius: 18px;
    overflow: hidden;
    position: relative;
  }

  /* Front */
  .card--front { background: var(--ink); display: flex; flex-direction: column; }
  .card--front .brand-area { flex: 1; display: flex; align-items: center; justify-content: center; }
  .brand-name {
    font-family: "Josefin Sans", sans-serif;
    font-weight: 600;
    letter-spacing: 0.08em;
    text-transform: uppercase;
    text-align: center;
    line-height: 1.25;
  }
  .card--front .brand-name { color: var(--white); font-size: 40px; }
  .web-band {
    height: 48px;
    background: var(--white);
    color: var(--ink);
    display: flex; align-items: center; justify-content: center;
    font-weight: 700; font-size: 15px; letter-spacing: 0.14em;
  }

  /* Back */
  .card--back { background: var(--ink); }
  .back-top {
    position: absolute; left: 0; right: 0; top: 0; height: 180px;
    background: var(--paper);
    display: flex; align-items: center; justify-content: center;
  }
  .card--back .brand-name { color: var(--ink); font-size: 30px; }
  .stripes { position: absolute; left: 0; right: 0; top: 180px; }
  .stripe { height: 4px; background: var(--white); margin-top: 6px; }
  .back-info {
    position: absolute; left: 0; right: 0; top: 214px; bottom: 0;
    display: flex; align-items: center; justify-content: center;
    color: var(--white);
  }
  .person { text-align: right; padding-right: 28px; }
  .person-name { font-size: 20px; font-weight: 300; }
  .person-name strong { font-weight: 700; }
  .person-title { font-size: 12px; color: var(--grey-light); margin-bottom: 10px; }
  .address { font-size: 14px; font-weight: 700; line-height: 1.35; }
  .divider { width: 2px; height: 112px; background: var(--white); }
  .contact { list-style: none; padding-left: 28px; font-size: 14px; font-weight: 300; color: var(--white); }
  .contact li { display: flex; align-items: center; gap: 12px; line-height: 1.85; }
  .contact svg { width: 14px; height: 14px; fill: var(--white); flex: none; }
</style>
</head>
<body>

<section class="card card--front" aria-label="Card front">
  <div class="brand-area">
    <p class="brand-name">Brightline<br>Tattoo Removal</p>
  </div>
  <div class="web-band">www.brightlinetattooremoval.example</div>
</section>

<section class="card card--back" aria-label="Card back">
  <div class="back-top">
    <p class="brand-name">Brightline<br>Tattoo Removal</p>
  </div>
  <div class="stripes">
    <div class="stripe"></div>
    <div class="stripe"></div>
    <div class="stripe"></div>
  </div>
  <div class="back-info">
    <div class="person">
      <p class="person-name">Melissa <strong>Thornbury</strong></p>
      <p class="person-title">Chief Executive Offer</p>
      <p class="address">4615 Oakmere Pkwy, Suite 210<br>Raleigh, NC 27654</p>
    </div>
    <div class="divider"></div>
    <ul class="contact">
      <li>
        <svg viewBox="0 0 16 16" aria-hidden="true"><path d="M1 5c0-2 2-3 7-3s7 1 7 3v1h-4V5H5v1H1zM4 7h8l2 7H2z"/></svg>
        919.537.2846
      </li>
      <li>
        <svg viewBox="0 0 16 16" aria-hidden="true"><path d="M1 5c0-2 2-3 7-3s7 1 7 3v1h-4V5H5v1H1zM4 7h8l2 7H2z"/></svg>
        919.362.4178
      </li>
      <li>
        <svg viewBox="0 0 16 16" aria-hidden="true"><path d="M4 1h8v4H4zM1 6h14v6h-3v3H4v-3H1zM5 10v3h6v-3z"/></svg>
        919.685.3907
      </li>
      <li>
        <svg viewBox="0 0 16 16" aria-hidden="true"><path d="M1 3h14v1L8 9 1 4zM1 6l7 5 7-5v7H1z"/></svg>
        mthornbury@brightlinetattooremoval.example
      </li>
    </ul>
  </div>
</section>

</body>
</html>
```